A website where experts collaborate on your project

I am building a new website where experts (yes, like designers) collaborate on projects with the project owner. More minds = more collaboration = better end product. Please see Pelmora(dot)com for a quick landing page I created for collaborating on presentations (although there will be many project types offered)

I am looking for a DESIGNER LONG TERM, but for now, just need initial mock ups to show the web programmers.

I have 21 Word documents loosely designed, what I would like to see here is a theme. Please DO NOT GO OFF WHAT YOU CURRENTLY SEE AT PELMORA. What is up now is only a quick landing page.

You can view a Word doc of the homepage here:
https://www.filevanta.com/s/qx83kdm2/home.docx?dl=0

WHAT AM I LOOKING FOR?
A clean, well designed theme.

Here is a link to the logo:
https://www.filevanta.com/s/mr47tpz9/logo%20-%20horizontal.tif?dl=0
-----------------------------------------
Here are a few sites I like the design of and what I like about them:
www.quenbrook.com-all around my favorite, beautiful graphics, clean layout, bold use of colors on a dark background
Ravelto.com- clean layout, The use of humans and bubble style elements.
Mintharbor.com :) clean, bold, unique pop art style but professional
plumevault.com - From the unique colors and artwork and the ability of that art to not interfere with the important elements of the site
sparkwidgets.com-clean, nice colors, well organized and separated sections.
www.dunmereco.com-love the font, use of colors and sectionalized style

All in all, I am not picky and open to so many styles. I would ultimately like the designer I pick to design all 21 pages.
Updates

Hello everyone,Moving forward, I would like you all to pay special attention to the section in my brief titled "Here are a few sites I like the design of and what I like about them". Please see below, I handpicked each one of these as sites I really like. Thank you.Here are a few sites I like the design of and what I like about them:Ravelto.com- clean layout, The use of humans and bubble style elements.Mintharbor.com :) clean, bold, unique pop art style but professionalwriteraccess.com - From the unique colors and artwork and the ability of that art to not interfere with the important elements of the sitegrowthgeeks.com-clean, nice colors, well organized and separated sections.www.dunmereco.com-love the font, use of colors and sectionalized stylewww.quenbrook.com-beautiful graphics, clean layout, bold use of colors----------------------------------------- Added Tuesday, November 24, 2015

I updated the homepage, you can see it here:https://www.dropbox.com/s/kwlkbsookq3cg2m/1new%20homepage.docx?dl=0I am modeling it after my favorite designed site: triplelift.comI love the dark colors with the orange glowing style boldness of the buttons. It's real clean too. Added Tuesday, November 24, 2015

Target Market(s)

small business owners, marketers, freelancer writers, graphic designers,

Industry/Entity Type

Building

Number of Pages Required

5+ page

Requirements
Must have
• I can't think of anything the project must have.
Nice to have
• WHAT AM I LOOKING FOR?
• A clean, well designed theme. I had a designer do a bit of work putting elements together, I found it to be very plain, but I like the Application Page (https://www.filevanta.com/s/jb19ckr3/Pelmora-Website.ai?dl=0)
• Here is a link to the logo:
• https://www.filevanta.com/s/mr47tpz9/logo%20-%20horizontal.tif?dl=0
• Here are a few sites I like the design of and what I like about them:
• Ravelto.com- clean layout, The use of humans and bubble style elements.
• Mintharbor.com :) clean, bold, unique pop art style but professional
• plumevault.com - From the unique colors and artwork and the ability of that art to not interfere with the important elements of the site
• sparkwidgets.com-clean, nice colors, well organized and separated sections.
• www.dunmereco.com-love the font, use of colors and sectionalized style
• www.quenbrook.com-beautiful graphics, clean layout, bold use of colors
• -----------------------------------------
Should not have
• out of the boxed, templated style website. I want this site to be memorable and not look like a thousand others

```html
<!DOCTYPE html>
<html lang="en">
<head>
<meta charset="utf-8">
<title>Pelmora – Convert More Customers</title>
<link rel="stylesheet" href="https://fonts.googleapis.com/css2?family=Raleway:wght@400;500;600;700&family=Open+Sans:wght@400;600&display=swap">
<style>
:root{
  --orange:#f7941d;
  --blue:#3aa3c8;
  --blue-dark:#2b87ab;
  --ink:#3a3a3a;
  --muted:#666;
  --rule:#d9d9d9;
  --footer:#232323;
  --white:#fff;
}
*{margin:0;padding:0;box-sizing:border-box}
html,body{width:837px;height:1200px;overflow:hidden;background:var(--white)}
body{position:relative;font-family:'Raleway',sans-serif;color:var(--ink)}
.abs{position:absolute}

/* header */
.site-header{position:absolute;left:0;top:0;width:837px;height:78px;background:var(--white)}
.brand{left:95px;top:30px;display:flex;align-items:center;gap:8px}
.brand-name{font-family:'Raleway',sans-serif;font-weight:700;font-size:21px;color:var(--orange);letter-spacing:.2px}
.brand-dot{width:46px;height:46px;border-radius:50%;background:var(--orange);margin-top:-24px}
.nav a{position:absolute;top:34px;font-size:12.5px;color:#555;text-decoration:none}
.nav .caret{display:inline-block;width:6px;height:6px;border-right:1px solid #777;border-bottom:1px solid #777;transform:rotate(45deg);margin:0 0 3px 5px}
.search{left:725px;top:34px}

/* hero */
.hero{left:0;top:78px;width:837px;height:357px;background:linear-gradient(100deg,#4a5866 0%,#6e7c88 40%,#8a96a1 65%,#5a6470 100%)}
.hero-title{left:102px;top:183px;font-size:30px;font-weight:400;color:var(--white)}
.hero-sub{left:103px;top:220px;font-size:17.5px;line-height:22px;color:var(--white);font-weight:400}
.btn-start{left:104px;top:278px;width:101px;height:27px;background:var(--blue);color:var(--white);font-size:12px;font-weight:600;display:flex;align-items:center;justify-content:center}
.dots{left:392px;top:414px;display:flex;gap:3px}
.dots span{width:10px;height:10px;border-radius:50%;background:#111}
.dots span:first-child{background:#eee}

/* filter */
.section-title{font-size:19px;font-weight:400}
.filter-title{left:95px;top:478px;color:var(--orange)}
.filter-label{font-size:12px;color:#333;display:flex;align-items:center;gap:6px}
.filter-label svg{flex:none}
.rule{left:94px;width:224px;height:1px;background:var(--rule)}
.price-track{left:124px;top:538px;width:164px;height:1px;background:#bbb}
.price-fill{left:124px;top:537px;width:67px;height:2px;background:var(--blue)}
.knob{width:10px;height:10px;border-radius:50%;background:#9fd4e6;border:1px solid var(--blue)}
.tiny{font-family:'Open Sans',sans-serif;font-size:8.5px;color:#333}
.country-list{left:113px;top:585px;list-style:none;font-family:'Open Sans',sans-serif;font-size:8px;color:#444;line-height:16.6px}

/* projects */
.projects-title{left:367px;top:478px;color:var(--blue)}
.project{left:367px;width:400px;height:56px}
.project-thumb{position:absolute;left:0;top:0;width:69px;height:53px;background:linear-gradient(135deg,#c7d3dc,#7e8f9c)}
.project-name{position:absolute;left:80px;top:0;font-size:11.5px;color:#333}
.project-desc{position:absolute;left:80px;top:17px;font-family:'Open Sans',sans-serif;font-size:8.4px;color:#555;white-space:nowrap}
.project-meta{position:absolute;left:80px;top:37px;font-family:'Open Sans',sans-serif;font-size:8.3px;color:var(--orange);white-space:nowrap}

/* testimonials */
.testimonials{left:0;top:934px;width:837px;height:184px;background:var(--orange);color:var(--white);text-align:center}
.testimonials h2{position:absolute;left:0;width:837px;top:34px;font-size:19px;font-weight:400}
.quote{position:absolute;left:150px;width:537px;top:70px;font-size:13px;line-height:21.5px}
.quote-mark{position:absolute;font-family:Georgia,serif;font-size:34px;font-weight:700;line-height:1}
.author{position:absolute;left:0;width:837px;top:116px;font-size:13px}

/* footer */
.site-footer{left:0;top:1118px;width:837px;height:82px;background:var(--footer)}
.footer-links{left:100px;top:17px;font-size:10.5px;color:#eee}
.copyright{left:100px;top:38px;font-family:'Open Sans',sans-serif;font-size:7.8px;color:#ccc}
.social{left:675px;top:18px;display:flex;gap:9px}
.social span{width:11px;height:11px;border-radius:50%;background:#eee}
</style>
</head>
<body>

<header class="site-header">
  <div class="brand abs">
    <span class="brand-name">Pelmora</span>
    <span class="brand-dot"></span>
  </div>
  <nav class="nav">
    <a style="left:332px">Browse<span class="caret"></span></a>
    <a style="left:410px">Projects</a>
    <a style="left:486px">How it Work</a>
    <a style="left:582px">Plans</a>
    <a style="left:644px">My Account</a>
  </nav>
  <svg class="search abs" width="14" height="14" viewBox="0 0 14 14" aria-label="Search"><circle cx="5.8" cy="5.8" r="4.3" fill="none" stroke="#555" stroke-width="2"/><line x1="9" y1="9" x2="13" y2="13" stroke="#555" stroke-width="2.2" stroke-linecap="round"/></svg>
</header>

<section class="hero abs" role="img" aria-label="Photo of a man in a striped shirt working at a laptop in an office">
</section>
<h1 class="hero-title abs">Convert More Customers</h1>
<p class="hero-sub abs">Experience the power of experts<br>collaborating on your project.</p>
<a class="btn-start abs">Get Started</a>
<div class="dots abs"><span></span><span></span><span></span><span></span></div>

<!-- filter -->
<h2 class="section-title filter-title abs">Filter</h2>

<div class="filter-label abs" style="left:98px;top:511px">
  <svg width="9" height="15" viewBox="0 0 9 15"><text x="0" y="13" font-family="Open Sans" font-weight="700" font-size="15" fill="#3aa3c8">$</text></svg>Price
</div>
<span class="tiny abs" style="left:96px;top:533px">$20</span>
<div class="price-track abs"></div>
<div class="price-fill abs"></div>
<div class="knob abs" style="left:119px;top:533px"></div>
<div class="knob abs" style="left:186px;top:533px"></div>
<span class="tiny abs" style="left:291px;top:533px">$1000+</span>
<div class="rule abs" style="top:556px"></div>

<div class="filter-label abs" style="left:93px;top:562px">
  <svg width="14" height="14" viewBox="0 0 14 14"><circle cx="7" cy="7" r="7" fill="#3aa3c8"/><path d="M4 3c2 1 1 3 3 3s1 3 3 4M3 9c1 0 2 1 2 3" stroke="#fff" stroke-width="1.3" fill="none"/></svg>Country
</div>
<ul class="country-list abs">
  <li>Australia</li><li>Paris</li><li>India</li><li>England</li><li>Spain</li><li>France</li>
</ul>
<div class="rule abs" style="top:688px"></div>

<div class="filter-label abs" style="left:94px;top:698px">
  <svg width="14" height="12" viewBox="0 0 14 12"><g fill="#3aa3c8"><rect y="1" width="14" height="2"/><rect y="5" width="14" height="2"/><rect y="9" width="14" height="2"/></g></svg>Category
</div>
<div class="rule abs" style="top:723px"></div>

<div class="filter-label abs" style="left:93px;top:732px">
  <svg width="14" height="14" viewBox="0 0 14 14"><circle cx="7" cy="7" r="6" fill="none" stroke="#3aa3c8" stroke-width="1.6"/><path d="M7 3.5V7H4.5" stroke="#3aa3c8" stroke-width="1.5" fill="none"/></svg>Time Left
</div>
<div class="rule abs" style="top:756px"></div>

<div class="filter-label abs" style="left:93px;top:766px">
  <svg width="14" height="14" viewBox="0 0 14 14"><circle cx="7" cy="7" r="7" fill="#3aa3c8"/><path d="M3.8 7.2l2.2 2.2 4.2-4.6" stroke="#fff" stroke-width="1.7" fill="none"/></svg>Active | Expired
</div>
<div class="rule abs" style="top:790px"></div>

<div class="filter-label abs" style="left:95px;top:800px">
  <svg width="12" height="14" viewBox="0 0 12 14"><path d="M3 6V4a3 3 0 0 1 6 0v2" stroke="#3aa3c8" stroke-width="1.8" fill="none"/><rect y="6" width="12" height="8" rx="1" fill="#3aa3c8"/></svg>Contains adult content
</div>
<div class="rule abs" style="top:823px"></div>

<div class="filter-label abs" style="left:94px;top:834px">
  <svg width="15" height="14" viewBox="0 0 15 14"><rect x="0.8" y="2.8" width="10.5" height="10.4" fill="none" stroke="#3aa3c8" stroke-width="1.4"/><path d="M5 9.5l1-2.5 6.5-6.5 1.5 1.5L7.5 8.5z" fill="#3aa3c8"/></svg>Keywords
</div>
<div class="rule abs" style="top:860px"></div>

<div class="filter-label abs" style="left:93px;top:868px">
  <svg width="17" height="14" viewBox="0 0 17 14"><g fill="#3aa3c8"><circle cx="8.5" cy="3.5" r="3"/><circle cx="3" cy="5" r="2.2"/><circle cx="14" cy="5" r="2.2"/><path d="M3.5 14a5 5 0 0 1 10 0z"/><path d="M0 12a3 3 0 0 1 4-3l-1 3z"/><path d="M17 12a3 3 0 0 0-4-3l1 3z"/></g></svg>Followers
</div>

<!-- projects -->
<h2 class="section-title projects-title abs">Crowd Projects</h2>

<article class="project abs" style="top:518px">
  <div class="project-thumb" role="img" aria-label="Photo of a businessman working at a laptop by a window"></div>
  <h3 class="project-name" style="font-weight:400">Ut ac mi quis lacus mollis</h3>
  <p class="project-desc">aliquam Curabitur iaculis tempus eros Curabitur vel mi sit amet sdad</p>
  <p class="project-meta">Price: $80 &nbsp;| &nbsp;Country: UK &nbsp;| &nbsp;Time Left: 6 dauys</p>
</article>

<article class="project abs" style="top:594px">
  <div class="project-thumb" role="img" aria-label="Photo of a man in a white shirt seated at a desk with a monitor"></div>
  <h3 class="project-name" style="font-weight:400">Fusce ultricies orci ac feugiat</h3>
  <p class="project-desc">aliquam Curabitur iaculis tempus eros Curabitur vel mi sit amet sdad</p>
  <p class="project-meta">Price: $80 &nbsp;| &nbsp;Country: UK &nbsp;| &nbsp;Time Left: 6 dauys</p>
</article>

<article class="project abs" style="top:667px">
  <div class="project-thumb" role="img" aria-label="Photo of hands writing on paper beside a laptop" style="background:linear-gradient(135deg,#6b4a38,#d8cfc6)"></div>
  <h3 class="project-name" style="font-weight:400">Quisque dignissim congue</h3>
  <p class="project-desc">aliquam Curabitur iaculis tempus eros Curabitur vel mi sit amet sdaed</p>
  <p class="project-meta">Price: $80 &nbsp;| &nbsp;Country: UK &nbsp;| &nbsp;Time Left: 6 dauys</p>
</article>

<article class="project abs" style="top:741px">
  <div class="project-thumb" role="img" aria-label="Photo of a man in a tie working at a laptop" style="background:linear-gradient(135deg,#eef1f4,#8fa2b3)"></div>
  <h3 class="project-name" style="font-weight:400">Aliquam erat volutpat</h3>
  <p class="project-desc">aliquam Curabitur iaculis tempus eros Curabitur vel mi sit amet sdaed</p>
  <p class="project-meta">Price: $80 &nbsp;| &nbsp;Country: UK &nbsp;| &nbsp;Time Left: 6 dauys</p>
</article>

<article class="project abs" style="top:820px">
  <div class="project-thumb" role="img" aria-label="Photo of a woman working at a laptop in a bright room" style="background:linear-gradient(135deg,#dfe7ee,#9fb3c2)"></div>
  <h3 class="project-name" style="font-weight:400">Aliquam erat volutpat</h3>
  <p class="project-desc">aliquam Curabitur iaculis tempus eros Curabitur vel mi sit amet sdaed</p>
  <p class="project-meta">Price: $80 &nbsp;| &nbsp;Country: UK &nbsp;| &nbsp;Time Left: 6 dauys</p>
</article>

<!-- testimonials -->
<section class="testimonials abs">
  <h2>Testimonials</h2>
  <span class="quote-mark" style="left:156px;top:67px">&ldquo;</span>
  <p class="quote">With Pelmora I have multiple experts perfecting my content and I only pay for the feedback I find valuable. It's perfect</p>
  <span class="quote-mark" style="left:543px;top:98px">&rdquo;</span>
  <p class="author">Dana Holt, CEO, Tallow 52</p>
</section>

<!-- footer -->
<footer class="site-footer abs">
  <p class="footer-links abs">Browse &nbsp;| &nbsp;Projects &nbsp;| &nbsp;How it Work &nbsp;| &nbsp;Plans &nbsp;| &nbsp;My Account</p>
  <p class="copyright abs">© 2015 Company Name &nbsp;All right reserved &nbsp;Term of Use</p>
  <div class="social abs" aria-label="Social links"><span></span><span></span><span></span><span></span></div>
</footer>

</body>
</html>
```